Brookmere Osteopathy flyer

I want a clean clear DL flyer (but also want an A4 poster) promoting a new Osteopathic business in a semi rural area in Tasmania (Australia).
It can have pictures like the examples attached to show people what Osteopathy is (its like Chiropractic and physiotherapy).
I am the sole practioner and am male, so any pictures would be best to be a white male if possible.
I've attached some wording, you can use all, or none of it
I don't have a phone number for the business yet
info@brookmereosteopathy.example
www.brookmereosteopathy.example
Target Market(s)
Australians, from tradies, professionals, babies to retired people
Industry/Entity Type
Health
Look and feel

```html
<!DOCTYPE html>
<html lang="en">
<head>
<meta charset="utf-8">
<title>Brookmere Osteopathy Flyer</title>
<link rel="stylesheet" href="https://fonts.googleapis.com/css2?family=Poppins:wght@400;500;600;700&family=Roboto:wght@700&display=swap">
<style>
  :root {
    --orange: #f58f3a;
    --blue: #1590d1;
    --ink: #1e1e1e;
    --paper: #ffffff;
    --stage: #e9e9e9;
  }
  * { margin: 0; padding: 0; box-sizing: border-box; }
  html, body { width: 1021px; height: 1200px; overflow: hidden; background: var(--stage); }
  body { font-family: "Poppins", sans-serif; color: var(--ink); position: relative; }

  .flyer {
    position: absolute; left: 86px; top: 0;
    width: 994px; height: 1405px;
    background: var(--paper);
    transform: scale(0.8541); transform-origin: 0 0;
    overflow: hidden;
  }
  .abs { position: absolute; }

  .hero-photo {
    left: 0; top: 220px; width: 994px; height: 690px;
    background: linear-gradient(160deg, #e3d9cf 0%, #cdb9a6 40%, #b9bcc0 75%, #d8d4cf 100%);
  }
  .shapes { left: 0; top: 0; width: 994px; height: 1405px; }

  .brand-mark {
    left: 70px; top: 69px; width: 220px; height: 220px;
    border: 3px solid var(--blue); border-radius: 50%;
    display: flex; align-items: center; justify-content: center; text-align: center;
  }
  .brand-name { font-weight: 700; font-size: 25px; line-height: 1.2; color: var(--blue); }

  .headline { left: 342px; top: 52px; font-weight: 700; line-height: 0.86; letter-spacing: -1px; }
  .headline .line-1 { display: block; font-size: 92px; color: var(--orange); }
  .headline .line-2 { display: block; font-size: 94px; color: var(--blue); }
  .subhead { left: 345px; top: 230px; font-size: 21.5px; font-weight: 500; line-height: 1.35; }

  .photo-circle { border-radius: 50%; border: 6px solid var(--paper); }
  .circle-a { left: 146px; top: 633px; width: 212px; height: 212px; background: linear-gradient(150deg, #c9c7c2, #8f9698 60%, #b7a596); }
  .circle-b { left: 376px; top: 617px; width: 242px; height: 242px; background: linear-gradient(150deg, #d8c0ad, #eeeeee 55%, #f6f6f6); }
  .circle-c { left: 634px; top: 633px; width: 214px; height: 214px; background: linear-gradient(180deg, #d9d4cf, #a9b4bd 45%, #e2dfda 70%, #d3d3d3); }

  .treatment-photo {
    left: 533px; top: 855px; width: 377px; height: 205px;
    border-radius: 0 0 12px 12px;
    background: linear-gradient(120deg, #5e6b66 0%, #9aa3a0 35%, #d9b39a 55%, #9fc8ee 80%, #b9d6f2 100%);
  }
  .about-box {
    left: 533px; top: 1066px; width: 377px; height: 180px;
    background: var(--orange); border-radius: 12px;
    padding: 30px 26px 0 31px;
    font-size: 17.5px; line-height: 1.22; font-weight: 500; color: var(--ink);
  }

  .reasons-title { left: 68px; top: 868px; font-weight: 700; font-size: 28.5px; line-height: 1.07; }
  .reasons-title .t1 { display: block; color: var(--orange); }
  .reasons-title .t2 { display: block; color: var(--blue); }

  .reason-list { left: 68px; top: 945px; width: 420px; display: grid; grid-template-columns: 228px 192px; row-gap: 14px; list-style: none; }
  .reason { display: flex; align-items: center; height: 47px; font-size: 13px; font-weight: 500; line-height: 1.17; }
  .reason-icon { flex: none; width: 45px; height: 45px; border: 1.6px solid var(--blue); border-radius: 50%; margin-right: 9px; display: flex; align-items: center; justify-content: center; }
  .reason-icon span { width: 10px; height: 10px; border: 1.6px solid var(--blue); border-radius: 50%; }

  .contact-bars { left: 68px; top: 1264px; width: 442px; }
  .bar { display: flex; align-items: center; height: 39px; padding-left: 14px; font-size: 19px; white-space: nowrap; }
  .bar svg { margin-right: 9px; flex: none; }
  .bar-address { background: var(--orange); border-radius: 8px 8px 0 0; color: var(--ink); }
  .bar-email { background: var(--blue); border-radius: 0 0 8px 8px; color: var(--paper); }

  .phone { left: 538px; top: 1250px; display: flex; align-items: center; }
  .phone-number { font-family: "Roboto", sans-serif; font-weight: 700; font-size: 60px; letter-spacing: -1px; color: var(--ink); margin-left: 4px; }
  .website { left: 541px; top: 1313px; display: flex; align-items: center; font-size: 21px; font-weight: 500; white-space: nowrap; }
  .website svg { margin-right: 9px; }
  .website .domain { color: var(--blue); font-weight: 600; }
</style>
</head>
<body>
<main class="flyer">
  <div class="abs hero-photo" role="img" aria-label="Osteopath treating a patient's lower back on a treatment table"></div>

  <svg class="abs shapes" viewBox="0 0 994 1405" aria-hidden="true">
    <path d="M0,0 H994 V232 C760,350 420,388 0,262 Z" fill="var(--orange)"/>
    <path d="M0,0 H994 V232 C740,338 420,372 0,254 Z" fill="var(--paper)"/>
    <path d="M0,826 C300,690 700,690 994,872 V1405 H0 Z" fill="var(--blue)"/>
    <path d="M0,838 C300,706 700,706 994,894 V1405 H0 Z" fill="var(--paper)"/>
  </svg>

  <div class="abs brand-mark"><span class="brand-name">Brookmere<br>Osteopathy</span></div>

  <h1 class="abs headline"><span class="line-1">Feel Better</span><span class="line-2">Move Freely</span></h1>
  <p class="abs subhead">Discover how osteopathy can help relieve<br>your pain and restore your movement.</p>

  <div class="abs photo-circle circle-a" role="img" aria-label="Osteopath assessing a patient's shoulder"></div>
  <div class="abs photo-circle circle-b" role="img" aria-label="Hands working on a patient's neck and shoulder"></div>
  <div class="abs photo-circle circle-c" role="img" aria-label="Leg stretch treatment on a table"></div>

  <div class="abs treatment-photo" role="img" aria-label="Osteopath assessing a patient's arm"></div>
  <p class="abs about-box">Osteopaths use a combination of joint manipulation, targeted deep tissue massage and stretching to improve function, relieve pain and support the body’s ability to heal itself.</p>

  <h2 class="abs reasons-title"><span class="t1">COMMON REASONS PEOPLE</span><span class="t2">VISIT AN OSTEOPATH:</span></h2>
  <ul class="abs reason-list">
    <li class="reason"><i class="reason-icon"><span></span></i>Back or<br>neck pain</li>
    <li class="reason"><i class="reason-icon"><span></span></i>Disc related<br>issues</li>
    <li class="reason"><i class="reason-icon"><span></span></i>Headaches<br>or migraines</li>
    <li class="reason"><i class="reason-icon"><span></span></i>Sciatica</li>
    <li class="reason"><i class="reason-icon"><span></span></i>Joint &amp;<br>muscle pain</li>
    <li class="reason"><i class="reason-icon"><span></span></i>Pregnancy<br>related<br>discomfort</li>
    <li class="reason"><i class="reason-icon"><span></span></i>Plantar<br>fasciitis</li>
    <li class="reason"><i class="reason-icon"><span></span></i>Adhesive<br>capsulitis</li>
    <li class="reason"><i class="reason-icon"><span></span></i>Tendonitis<br>or Bursitis</li>
    <li class="reason"><i class="reason-icon"><span></span></i>Tennis or<br>Golfers<br>elbow</li>
  </ul>

  <div class="abs contact-bars">
    <div class="bar bar-address">
      <svg width="16" height="18" viewBox="0 0 16 18"><path d="M8 1a6 6 0 0 0-6 6c0 4.5 6 10 6 10s6-5.5 6-10a6 6 0 0 0-6-6z" fill="#fff"/><circle cx="8" cy="7" r="2.3" fill="var(--orange)"/></svg>
      27 Millbrook Lane, Brookmere
    </div>
    <div class="bar bar-email">
      <svg width="17" height="17" viewBox="0 0 17 17"><circle cx="8.5" cy="8.5" r="8.5" fill="#fff"/><rect x="4" y="5.5" width="9" height="6" rx="1" fill="none" stroke="var(--blue)" stroke-width="1.4"/><path d="M4.5 6l4 3 4-3" fill="none" stroke="var(--blue)" stroke-width="1.4"/></svg>
      info@brookmereosteopathy.example
    </div>
  </div>

  <div class="abs phone">
    <svg width="26" height="26" viewBox="0 0 26 26"><circle cx="13" cy="13" r="13" fill="var(--blue)"/><path d="M9 7.5l2.5 2.2-1.4 2.2c.9 1.7 2.2 3 3.9 3.9l2.2-1.4 2.2 2.5-1.6 2c-4.8-.6-8.7-4.5-9.3-9.3z" fill="#fff"/></svg>
    <span class="phone-number">0400 555 019</span>
  </div>
  <div class="abs website">
    <svg width="20" height="20" viewBox="0 0 20 20" fill="none" stroke="var(--blue)" stroke-width="1.6"><circle cx="10" cy="10" r="8.5"/><ellipse cx="10" cy="10" rx="3.6" ry="8.5"/><path d="M1.5 10h17M3 5.5h14M3 14.5h14"/></svg>
    <span>www.<span class="domain">brookmereosteopathy</span>.example</span>
  </div>
</main>
</body>
</html>
```